Landing Page Design for Adult Dating Age Verification (18+)

The objective of this task is to design a visually appealing pre-landing page for the adult dating site "Quillmera (site: https://quillmera.com/)" with an age verification mechanism. The pre-landing page will feature two buttons that redirect visitors to the main offer. The design should also include a footer block that includes links to the terms of use, privacy policy, and contact us pages.

Design Requirements:
Develop an age verification section prominently displayed on the pre-landing page.
Design the section to include two buttons labeled "Yes" and "No" for visitors to confirm their age.
Ensure the section is visually appealing and clearly communicates the purpose of age verification.

Visual Appeal:
Create a visually appealing design that aligns with the branding and theme of the "Quillmera" adult dating site.
Use suitable color schemes, typography, and graphics to enhance the overall visual appeal of the pre-landing page.

Layout and Navigation:
Design an engaging and intuitive layout that encourages visitors to interact with the page and proceed to the main offer.
Ensure clear and visible navigation elements that direct visitors to the main offer or provide additional information.

Responsive Design:
Develop a responsive design that provides a seamless user experience across various devices, including desktop and mobile.
Ensure the design elements and layout adapt well to different screen sizes and resolutions.

File Formats and Assets:
Deliver the final design in PSD, AI, or Sketch format, ensuring that the files are well-organized and layered.
Include any necessary images or assets used in the design, ensuring they are of high quality and optimized for web use.

```html
<!DOCTYPE html>
<html lang="en">
<head>
<meta charset="utf-8">
<title>Quillmera — Age Verification</title>
<link rel="stylesheet" href="https://fonts.googleapis.com/css2?family=DM+Serif+Display&family=Poppins:wght@400;500&display=swap">
<style>
  :root {
    --lilac: #d9bfe0;
    --lilac-dark: #c7a6d0;
    --ink: #16161e;
    --white: #ffffff;
    --black: #000000;
    --panel: rgba(255,255,255,0.86);
  }
  * { box-sizing: border-box; margin: 0; padding: 0; }
  html, body { width: 1200px; height: 903px; overflow: hidden; background: var(--white); }
  body { position: relative; font-family: "Poppins", sans-serif; color: var(--ink); }

  .site-header {
    position: absolute; left: 0; top: 0; width: 1200px; height: 87px;
    background: var(--white);
  }
  .brand {
    position: absolute; display: flex; align-items: center; gap: 10px;
    font-family: "DM Serif Display", serif; text-decoration: none;
  }
  .brand-dot { width: 60px; height: 60px; border-radius: 50%; background: var(--lilac); flex: none; }
  .site-header .brand { left: 98px; top: 13px; font-size: 33px; color: var(--ink); }
  .main-nav { position: absolute; top: 28px; left: 0; width: 100%; height: 30px; font-size: 16px; }
  .main-nav a, .main-nav span { position: absolute; color: var(--ink); text-decoration: none; line-height: 30px; }
  .nav-signin { left: 830px; }
  .nav-join { left: 927px; font-weight: 500; }
  .nav-lang { left: 1030px; }
  .nav-lang svg { vertical-align: middle; margin-left: 4px; }

  .hero {
    position: absolute; left: 0; top: 87px; width: 1200px; height: 596px;
    background:
      radial-gradient(ellipse at 62% 45%, #d9b8a6 0%, rgba(217,184,166,0) 45%),
      linear-gradient(110deg, #8a7c8c 0%, #b9a6ae 30%, #c7a69b 55%, #7c6276 80%, #5e4560 100%);
  }

  .age-panel {
    position: absolute; left: 296px; top: 274px; width: 608px; height: 225px;
    background: var(--panel); border-radius: 17px; text-align: center;
  }
  .age-title {
    font-family: "DM Serif Display", serif; font-weight: 400; font-size: 39px;
    line-height: 1; margin-top: 32px; color: var(--black);
  }
  .age-actions { display: flex; justify-content: center; gap: 10px; margin-top: 20px; }
  .age-btn {
    width: 69px; height: 51px; background: var(--lilac); border: none;
    font-family: "Poppins", sans-serif; font-size: 15px; color: var(--ink);
  }
  .remember {
    display: flex; justify-content: center; align-items: center; gap: 11px;
    margin-top: 23px; font-size: 15px; font-weight: 500;
  }
  .remember-box { width: 21px; height: 21px; background: var(--lilac-dark); }

  .site-footer {
    position: absolute; left: 0; top: 683px; width: 1200px; height: 220px;
    background: var(--black); color: var(--white); text-align: center;
    font-family: "DM Serif Display", serif;
  }
  .site-footer .brand {
    left: 50%; transform: translateX(-50%); top: 43px; font-size: 34px; color: var(--white);
  }
  .site-footer .brand-dot { width: 52px; height: 52px; }
  .footer-links { position: absolute; top: 115px; left: 0; width: 100%; display: flex; justify-content: center; gap: 40px; font-size: 16px; }
  .footer-links a { color: var(--white); text-decoration: none; }
  .copyright { position: absolute; top: 160px; left: 0; width: 100%; font-size: 16px; }
  .build-code { position: absolute; right: 46px; top: 167px; font-family: "Poppins", sans-serif; font-size: 11px; font-weight: 500; }
</style>
</head>
<body>
  <header class="site-header">
    <a class="brand" href="https://quillmera.com/"><span class="brand-dot"></span>Quillmera</a>
    <nav class="main-nav">
      <a class="nav-signin" href="#">Sign in</a>
      <a class="nav-join" href="#">Join Now</a>
      <span class="nav-lang">English<svg width="10" height="7" viewBox="0 0 10 7"><path d="M0 0h10L5 7z" fill="#16161e"/></svg></span>
    </nav>
  </header>

  <section class="hero" role="img" aria-label="Photo of a couple embracing on a bed beside a window"></section>

  <div class="age-panel">
    <h1 class="age-title">Are you over 18 years of age?</h1>
    <div class="age-actions">
      <button class="age-btn">Yes</button>
      <button class="age-btn">No</button>
    </div>
    <label class="remember"><span class="remember-box"></span>Remember me</label>
  </div>

  <footer class="site-footer">
    <a class="brand" href="https://quillmera.com/"><span class="brand-dot"></span>Quillmera</a>
    <div class="footer-links">
      <a href="#">Terms of Use</a>
      <a href="#">Privacy Policy</a>
      <a href="#">Contact us</a>
    </div>
    <p class="copyright">Copyrights@2023.Quillmera.All Rights Reserved</p>
    <span class="build-code">C56</span>
  </footer>
</body>
</html>
```